Label for kQm Ranch beef tallow

I need a small label to go on a 2oz amber glass jar as well as a 4 oz. amber glass jar of moisturizer.
I prefer it to be rectangular for the 2oz jar since it's small and square for the 4oz jar.
I'd like to keep our kQm Ranch logo the same font and style, which is attached. Ten Sleep, Wyoming should be left out. The font for kQm Ranch is spartan.
The label content is as follows:
Signature Tallow
Whipped Moisturizer
Ingredients: Beef Tallow, jojoba oil, peppermint oil.
2oz. jar

Instead of a white label, I'm thinking of a tan or brown label that will blend in with the amber jar. The lettering could then be a white, cream or even rust/burgandy color. Something to give it a rich look.

Thank you!

Target Market(s)

Mainly women but men as well.

Industry/Entity Type

Ranching and online beef sales

Requirements
Must have
• kQm Ranch logo

```html
<!DOCTYPE html>
<html lang="en">
<head>
<meta charset="UTF-8">
<title>kQm Ranch – Signature Tallow Labels</title>
<link rel="stylesheet" href="https://fonts.googleapis.com/css2?family=League+Spartan:wght@300&family=Arimo:wght@400;500&family=Allison&display=swap">
<style>
  :root {
    --canvas-bg: #e6e6e6;
    --label-bg: #000000;
    --label-ink: #ffffff;
  }
  * { box-sizing: border-box; margin: 0; padding: 0; }
  html, body {
    width: 1200px;
    height: 1200px;
    overflow: hidden;
    background: var(--canvas-bg);
  }
  .sheet {
    width: 1200px;
    height: 1200px;
    display: flex;
    align-items: center;
    justify-content: center;
    gap: 48px;
  }
  .label {
    background: var(--label-bg);
    color: var(--label-ink);
    position: relative;
    display: flex;
    flex-direction: column;
    align-items: center;
    text-align: center;
  }
  .brand {
    font-family: "League Spartan", sans-serif;
    font-weight: 300;
    line-height: 0.9;
    display: flex;
    flex-direction: column;
    align-items: center;
  }
  .product-name {
    font-family: "Arimo", Arial, sans-serif;
    font-weight: 500;
    letter-spacing: 0.2px;
  }
  .ingredients, .size {
    font-family: "Arimo", Arial, sans-serif;
    font-weight: 500;
  }
  .script {
    font-family: "Allison", cursive;
    font-weight: 400;
    white-space: nowrap;
  }

  /* 2oz rectangular label */
  .label--small {
    width: 516px;
    height: 282px;
    border-radius: 34px;
    justify-content: center;
    padding-top: 8px;
  }
  .label--small .brand-mark { font-size: 96px; }
  .label--small .brand-word { font-size: 50px; margin-top: 4px; }
  .label--small .product-name { font-size: 26px; margin-top: 10px; }
  .label--small .size { font-size: 13px; margin-top: 6px; }
  .label--small .script {
    position: absolute;
    left: 28px;
    top: 50%;
    font-size: 40px;
    transform: translate(-50%, -50%) rotate(-90deg) translateY(28px);
    transform-origin: center;
  }
  .label--small .ingredients {
    position: absolute;
    right: 38px;
    top: 50%;
    font-size: 11px;
    white-space: nowrap;
    transform: translate(50%, -50%) rotate(-90deg);
  }

  /* 4oz square label */
  .label--large {
    width: 516px;
    height: 516px;
    border-radius: 34px;
    padding-top: 30px;
  }
  .label--large .script { font-size: 60px; line-height: 1; }
  .label--large .brand { margin-top: 26px; }
  .label--large .brand-mark { font-size: 150px; }
  .label--large .brand-word { font-size: 60px; margin-top: 6px; }
  .label--large .product-name { font-size: 33px; margin-top: 34px; }
  .label--large .ingredients { font-size: 19px; margin-top: 6px; }
  .label--large .size { font-size: 17px; margin-top: 18px; }
</style>
</head>
<body>
  <main class="sheet">
    <section class="label label--small" aria-label="2oz jar label">
      <p class="script">Signature Tallow</p>
      <div class="brand">
        <span class="brand-mark">kQm</span>
        <span class="brand-word">RANCH</span>
      </div>
      <p class="product-name">WHIPPED MOISTURIZER</p>
      <p class="size">2oz.</p>
      <p class="ingredients">Beef Tallow, jojoba oil, peppermint oil</p>
    </section>

    <section class="label label--large" aria-label="4oz jar label">
      <p class="script">Signature Tallow</p>
      <div class="brand">
        <span class="brand-mark">kQm</span>
        <span class="brand-word">RANCH</span>
      </div>
      <p class="product-name">WHIPPED MOISTURIZER</p>
      <p class="ingredients">Beef Tallow, jojoba oil, peppermint oil</p>
      <p class="size">4oz.</p>
    </section>
  </main>
</body>
</html>
```